Northfield Builders Guild Business card

We are looking for a new business card design with photo included.
Our business is a nonprofit construction contractor membership organization. We offer business education, assist with business setup and licensing, provide safety training, and provide a member directory.
URL: www.builderslinkguild.org
Color code:
CMYK: 0 cyan, 42 magenta, 100 yellow, 0 black for Print.
Hexidecimal: #FF9900
RGB: R 255; G 153; B 0

```html
<!DOCTYPE html>
<html lang="en">
<head>
<meta charset="utf-8">
<title>Northfield Builders Guild – Business Card</title>
<link rel="stylesheet" href="https://fonts.googleapis.com/css2?family=Montserrat:wght@700;800;900&family=Arimo:wght@400&display=swap">
<style>
  :root {
    --guild-orange: #ff9900;
    --card-orange: #f7981d;
    --ink: #0c0c0c;
    --paper-white: #ffffff;
    --backdrop: #2a2a2a;
  }
  * { box-sizing: border-box; margin: 0; padding: 0; }
  html, body { width: 1200px; height: 1015px; overflow: hidden; }
  body {
    background: var(--backdrop);
    font-family: "Montserrat", Arial, sans-serif;
    position: relative;
  }
  .card {
    position: absolute;
    left: 220px;
    width: 760px;
    height: 434px;
    overflow: hidden;
    box-shadow: 0 12px 30px rgba(0,0,0,.5);
  }
  .card--front { top: 50px; background: var(--ink); }
  .card--back { top: 531px; background: var(--card-orange); }

  /* front */
  .front-brand {
    position: absolute;
    top: 70px; left: 0; right: 0;
    text-align: center;
    color: var(--paper-white);
    font-weight: 900;
    font-size: 58px;
    line-height: 1.05;
    letter-spacing: -1px;
    text-transform: uppercase;
  }
  .services {
    position: absolute;
    left: 0; right: 0; bottom: 0;
    height: 132px;
    background: var(--card-orange);
    display: flex;
    flex-wrap: wrap;
    align-content: center;
    justify-content: center;
    gap: 14px 34px;
    padding: 0 50px;
    list-style: none;
  }
  .services li {
    display: flex;
    align-items: center;
    gap: 8px;
    color: var(--ink);
    font-weight: 700;
    font-size: 17px;
    text-transform: uppercase;
  }
  .services li::before {
    content: "";
    width: 13px; height: 13px;
    border-radius: 50%;
    background: var(--ink);
  }

  /* back */
  .back-head {
    position: absolute;
    top: 0; left: 0; right: 0;
    height: 168px;
    background: var(--ink);
    display: flex;
    align-items: center;
    padding-left: 56px;
  }
  .back-brand {
    color: var(--paper-white);
    font-weight: 900;
    font-size: 40px;
    letter-spacing: -1px;
    text-transform: uppercase;
  }
  .person {
    position: absolute;
    top: 196px; left: 56px;
    color: var(--ink);
    text-transform: uppercase;
  }
  .person-name { font-weight: 900; font-size: 28px; line-height: 1.1; }
  .person-role { font-weight: 800; font-size: 17px; margin-top: 2px; }
  .contacts {
    position: absolute;
    top: 292px; left: 56px;
    list-style: none;
    font-family: "Arimo", Arial, sans-serif;
    font-size: 19px;
    color: var(--ink);
  }
  .contacts li { display: flex; align-items: center; gap: 10px; height: 28px; }
  .contact-icon { width: 22px; height: 22px; flex: none; }
  .address {
    position: absolute;
    top: 232px; right: 60px;
    width: 300px;
    font-family: "Arimo", Arial, sans-serif;
    font-style: normal;
    font-size: 19px;
    line-height: 1.35;
    color: var(--ink);
  }
  .website { display: block; margin-top: 14px; color: var(--ink); text-decoration: none; }
</style>
</head>
<body>
  <section class="card card--front" aria-label="Card front">
    <h1 class="front-brand">Northfield<br>Builders Guild</h1>
    <ul class="services">
      <li>Business education</li>
      <li>Assist with business setup and licensing</li>
      <li>Provide safety training</li>
      <li>Provide a member directory</li>
    </ul>
  </section>

  <section class="card card--back" aria-label="Card back">
    <header class="back-head">
      <p class="back-brand">Northfield Builders Guild</p>
    </header>
    <div class="person">
      <p class="person-name">Daniel Harper</p>
      <p class="person-role">Managing Director</p>
    </div>
    <ul class="contacts">
      <li>
        <svg class="contact-icon" viewBox="0 0 22 22" aria-hidden="true"><circle cx="11" cy="11" r="11" fill="#0c0c0c"/><path d="M7 6.5c.8-.8 1.6-.3 2 .5l.6 1.3c.2.5 0 1-.4 1.3l-.5.4c.5 1.2 1.5 2.2 2.7 2.7l.4-.5c.3-.4.8-.6 1.3-.4l1.3.6c.8.4 1.3 1.2.5 2-2 2-8.9-4.9-7.9-7.9z" fill="#f7981d"/></svg>
        (555) 214-3807
      </li>
      <li>
        <svg class="contact-icon" viewBox="0 0 22 22" aria-hidden="true"><circle cx="11" cy="11" r="11" fill="#0c0c0c"/><rect x="7.5" y="5" width="7" height="12" rx="1.2" fill="none" stroke="#f7981d" stroke-width="1.4"/><circle cx="11" cy="14.8" r=".8" fill="#f7981d"/></svg>
        800-555-0142
      </li>
      <li>
        <svg class="contact-icon" viewBox="0 0 22 22" aria-hidden="true"><circle cx="11" cy="11" r="11" fill="#0c0c0c"/><rect x="8" y="5.5" width="6" height="3.5" fill="#f7981d"/><rect x="5.5" y="9" width="11" height="5" rx="1" fill="#f7981d"/><rect x="8" y="13" width="6" height="3.5" fill="#0c0c0c" stroke="#f7981d" stroke-width="1"/></svg>
        555.310.0196
      </li>
      <li>
        <svg class="contact-icon" viewBox="0 0 22 22" aria-hidden="true"><circle cx="11" cy="11" r="11" fill="#0c0c0c"/><rect x="5.5" y="7" width="11" height="8" fill="#f7981d"/><path d="M5.5 7l5.5 4.5L16.5 7" fill="none" stroke="#0c0c0c" stroke-width="1"/></svg>
        hello@nbguild.org
      </li>
    </ul>
    <address class="address">
      2400 Ridgeway Ave<br>
      Suite #210, Fairview<br>
      OR 97024
      <a class="website" href="http://www.builderslinkguild.org">www.builderslinkguild.org</a>
    </address>
  </section>
</body>
</html>
```